Orbix Business Card design needed

I want to have my new business card designed to look like the Orbix lock screen. The front will contain my logo but just the (K) design not all the wording (attached) in the center of the card(screen) and the slide to unlock will be pointer in orange and then Brannock Insurance Inc. Not sure about the rest of the front of the card. Guessing some random date and the service bars I will leave up to your creative minds to come up with some cool. I am an insurance agency. For the back of the card I want it to look like a contact within an Orbix (picture and contact information,address etc..) I think you get the point. My name is Dale Brannock. Cell is 555-208-6127 Office 555-706-1294 (fax number is (555) 384-0716 address is UPDATE Website is www.brannockinsurance.example.

If you not sure what I am looking for google Orbix business card images or see samples I uploaded.

Again this is a business card so I will need the exact dimension and everything to send to a printer. File must be PRINT ready so please make sure it has smooth edges(no buttons on side of Orbix)
Updates

New Address is 
2718 Marigold Lane
Suite 410
Indianapolis
IN
46918

Please use this in your design.

email that needs to go on card is Dale@brannockinsurance.example If you are submitting designs please make sure it is new vx4 update design for the oRbix.

Reason: Need to extend for a few days.

Industry/Entity Type

Insurance

Requirements
Must have
• I am open to seeing designs with the font provide along with the standard Orbix font. Must use my colors. I would like to see designs with the standard Orbix contact colors but also with my colors. Have fun with the design if you can. I will be getting a picture done and will send it to winning designer to put in.
Should not have
• Do not want a standard square card. Make it look like an Orbix 5 shape please. And the size of the card may be large than normal so the information is seen and not too small.

```html
<!DOCTYPE html>
<html lang="en">
<head>
<meta charset="utf-8">
<title>Brannock Insurance – Lock Screen and Contact Cards</title>
<link rel="stylesheet" href="https://fonts.googleapis.com/css2?family=Arimo:wght@400;700&display=swap">
<style>
  :root {
    --page: #ffffff;
    --screen: #ffffff;
    --ink: #111111;
    --orange: #f26a10;
    --muted: #c9c6c4;
    --tint: #f8f1ef;
    --rule: #d9d9d9;
    --tab-bg: #f7f7f7;
    --tab-ink: #8e8e8e;
  }
  * { box-sizing: border-box; margin: 0; padding: 0; }
  html, body {
    width: 1200px; height: 1000px; overflow: hidden;
    background: var(--page);
    font-family: "Arimo", "Helvetica Neue", Arial, sans-serif;
    color: var(--ink);
  }
  .canvas { position: relative; width: 1200px; height: 1000px; }
  .screen {
    position: absolute; top: 155px; width: 384px; height: 680px;
    background: var(--screen); overflow: hidden;
    box-shadow: 0 0 0 1px #e6e6e6;
  }
  .screen--lock { left: 100px; }
  .screen--contact { left: 698px; }

  .status-bar {
    position: absolute; top: 0; left: 0; right: 0; height: 30px;
    font-size: 14px; display: flex; align-items: center;
    padding: 0 8px; z-index: 2;
  }
  .status-bar__carrier { display: flex; align-items: center; gap: 5px; }
  .status-bar__signal { letter-spacing: -1px; font-size: 10px; }
  .status-bar__time {
    position: absolute; left: 0; right: 0; text-align: center;
    font-weight: 700; pointer-events: none;
  }
  .status-bar__power { margin-left: auto; display: flex; align-items: center; gap: 6px; }

  .lock__backdrop { position: absolute; inset: 0; }
  .lock__mark {
    position: absolute; left: 82px; top: 135px;
    width: 220px; height: 220px; border-radius: 50%;
    background: var(--orange);
  }
  .lock__name {
    position: absolute; top: 402px; left: 0; right: 0; text-align: center;
    font-size: 26px; font-weight: 700; color: var(--orange);
  }
  .lock__slider {
    position: absolute; top: 540px; left: 88px;
    font-size: 25px; color: var(--muted);
    display: flex; align-items: center; gap: 14px;
  }
  .lock__grabber { position: absolute; top: 645px; left: 172px; }

  .contact__header {
    position: absolute; top: 30px; left: 0; right: 0; height: 23px;
    background: #f9f9f9; border-bottom: 1px solid var(--rule);
  }
  .contact__avatar {
    position: absolute; left: 28px; top: 75px;
    width: 106px; height: 106px; border-radius: 50%;
    background: var(--orange);
  }
  .contact__name {
    position: absolute; left: 164px; top: 118px;
    font-size: 28px; font-weight: 400;
  }
  .contact__fields { position: absolute; left: 33px; top: 212px; list-style: none; }
  .contact__field { margin-bottom: 11px; font-size: 19px; line-height: 25px; }
  .contact__label { color: var(--orange); display: block; }
  .contact__value { display: block; }

  .tab-bar {
    position: absolute; left: 0; right: 0; bottom: 0; height: 60px;
    background: var(--tab-bg); border-top: 1px solid var(--rule);
    display: flex;
  }
  .tab-bar__item {
    flex: 1; display: flex; flex-direction: column; align-items: center;
    justify-content: flex-end; padding-bottom: 4px;
    font-size: 11.5px; color: var(--tab-ink); gap: 3px;
  }
  .tab-bar__item--active { color: var(--orange); }
</style>
</head>
<body>
<main class="canvas">

  <section class="screen screen--lock" aria-label="Lock screen card front">
    <svg class="lock__backdrop" width="384" height="680" viewBox="0 0 384 680" aria-hidden="true">
      <path d="M0 580 C 230 540 370 360 384 170 L384 680 L0 680 Z" fill="var(--tint)"/>
    </svg>
    <header class="status-bar">
      <span class="status-bar__carrier"><span class="status-bar__signal">●●●○○</span> NOVA
        <svg width="14" height="11" viewBox="0 0 14 11"><path d="M1 4a9 9 0 0 1 12 0M3.3 6.3a5.5 5.5 0 0 1 7.4 0" stroke="#111" stroke-width="1.6" fill="none"/><circle cx="7" cy="9" r="1.5" fill="#111"/></svg>
      </span>
      <span class="status-bar__time">4:21 PM</span>
      <span class="status-bar__power">
        <svg width="8" height="13" viewBox="0 0 8 13"><path d="M1 4l6 5-3 3V1l3 3-6 5" stroke="#111" stroke-width="1.2" fill="none"/></svg>
        100%
        <svg width="28" height="12" viewBox="0 0 28 12"><rect x="0.5" y="0.5" width="24" height="11" rx="2" fill="none" stroke="#111"/><rect x="2" y="2" width="21" height="8" fill="#111"/><rect x="25.5" y="4" width="2" height="4" fill="#111"/></svg>
      </span>
    </header>
    <div class="lock__mark" aria-hidden="true"></div>
    <p class="lock__name">Brannock Insurance Inc.</p>
    <p class="lock__slider">
      <svg width="9" height="18" viewBox="0 0 9 18"><path d="M1 1l7 8-7 8" stroke="var(--muted)" stroke-width="1.6" fill="none"/></svg>
      slide to unlock
    </p>
    <svg class="lock__grabber" width="42" height="12" viewBox="0 0 42 12" aria-hidden="true"><path d="M3 9 Q21 0 39 9" stroke="var(--muted)" stroke-width="4" stroke-linecap="round" fill="none"/></svg>
  </section>

  <section class="screen screen--contact" aria-label="Contact card back">
    <header class="status-bar">
      <span class="status-bar__carrier"><span class="status-bar__signal">●●●○○</span> NOVA
        <svg width="14" height="11" viewBox="0 0 14 11"><path d="M1 4a9 9 0 0 1 12 0M3.3 6.3a5.5 5.5 0 0 1 7.4 0" stroke="#111" stroke-width="1.6" fill="none"/><circle cx="7" cy="9" r="1.5" fill="#111"/></svg>
      </span>
      <span class="status-bar__time">4:21 PM</span>
      <span class="status-bar__power">
        <svg width="8" height="13" viewBox="0 0 8 13"><path d="M1 4l6 5-3 3V1l3 3-6 5" stroke="#111" stroke-width="1.2" fill="none"/></svg>
        100%
        <svg width="28" height="12" viewBox="0 0 28 12"><rect x="0.5" y="0.5" width="24" height="11" rx="2" fill="none" stroke="#111"/><rect x="2" y="2" width="21" height="8" fill="#111"/><rect x="25.5" y="4" width="2" height="4" fill="#111"/></svg>
      </span>
    </header>
    <div class="contact__header" aria-hidden="true"></div>
    <div class="contact__avatar" aria-hidden="true"></div>
    <h1 class="contact__name">Dale Brannock</h1>
    <ul class="contact__fields">
      <li class="contact__field"><span class="contact__label">mobile</span><span class="contact__value">555 208 6127</span></li>
      <li class="contact__field"><span class="contact__label">office</span><span class="contact__value">555 706 1294</span></li>
      <li class="contact__field"><span class="contact__label">fax</span><span class="contact__value">(555) 384 0716</span></li>
      <li class="contact__field"><span class="contact__label">address</span><span class="contact__value">2718 Marigold Lane, Ste 410</span><span class="contact__value">Indianapolis, IN 46918</span></li>
      <li class="contact__field"><span class="contact__label">website</span><span class="contact__value">www.brannockinsurance.example</span></li>
      <li class="contact__field"><span class="contact__label">email</span><span class="contact__value">Dale@brannockinsurance.example</span></li>
    </ul>
    <nav class="tab-bar">
      <span class="tab-bar__item">
        <svg width="32" height="30" viewBox="0 0 32 30"><path d="M16 2l4 9.5 10 .8-7.6 6.6 2.4 9.8L16 23.5 7.2 28.7l2.4-9.8L2 12.3l10-.8z" fill="none" stroke="var(--tab-ink)" stroke-width="1.3"/></svg>
        Favorites</span>
      <span class="tab-bar__item">
        <svg width="30" height="30" viewBox="0 0 30 30"><circle cx="15" cy="15" r="13.5" fill="none" stroke="var(--tab-ink)" stroke-width="1.3"/><path d="M15 6v10h-6" fill="none" stroke="var(--tab-ink)" stroke-width="1.3"/></svg>
        Recents</span>
      <span class="tab-bar__item tab-bar__item--active">
        <svg width="30" height="30" viewBox="0 0 30 30"><circle cx="15" cy="15" r="15" fill="var(--orange)"/><circle cx="15" cy="11" r="5" fill="#fff"/><path d="M6 25a9 8 0 0 1 18 0z" fill="#fff"/></svg>
        Contacts</span>
      <span class="tab-bar__item">
        <svg width="30" height="30" viewBox="0 0 30 30" fill="none" stroke="var(--tab-ink)" stroke-width="1.1"><circle cx="5" cy="5" r="3.3"/><circle cx="15" cy="5" r="3.3"/><circle cx="25" cy="5" r="3.3"/><circle cx="5" cy="15" r="3.3"/><circle cx="15" cy="15" r="3.3"/><circle cx="25" cy="15" r="3.3"/><circle cx="5" cy="25" r="3.3"/><circle cx="15" cy="25" r="3.3"/><circle cx="25" cy="25" r="3.3"/></svg>
        Keypad</span>
      <span class="tab-bar__item">
        <svg width="38" height="30" viewBox="0 0 38 30"><circle cx="10" cy="16" r="7" fill="none" stroke="var(--tab-ink)" stroke-width="1.3"/><circle cx="28" cy="16" r="7" fill="none" stroke="var(--tab-ink)" stroke-width="1.3"/><path d="M10 23h18" stroke="var(--tab-ink)" stroke-width="1.3"/></svg>
        Voicemail</span>
    </nav>
  </section>

</main>
</body>
</html>
```